Sunleaf Pressery Remarketing and Retargeting ads.

We are a raw, cold pressed, organic juice company. We literally have the best product on the market and we need better ads. We have a new website in development and need remarking and retargeting ads. We have many more projects to follow. We are a healing company that helps people heal holistically. We are organic, raw, cold pressed, no hpp, served in glass.
Our existing site is: www.sunleafpressery.com
our site in development is: http://slpbeta.client.quillhostpanel.com
The ad sizes we need are:
120x600
160x600
300x600
336x280
300x250
320x50
468x60
970x90
We have 27 different juices, 6 different soups, 11 shots. Our primary business is juice and bone broth soup which is very popular. I can provide the individual bottles as well. We are looking for A+ work. Very excited to see what you come up with.
This is a google drive with more artwork.
https://files.examplecloud.net/folderview?id=7Kq_Rt2WpXnLmVbQeZsTyHuJcDfG&usp=sharing_eid&ts=84ab3f21
Updates
Here is a link to our more artwork of our products:
Target Market(s)
25-60, 80% female, 20% male, affluent Americans, making between $70,000-$500,000 annually
Industry/Entity Type
It Company
Number of Pages Required
1 page
Requirements
Must have
- There should be a different ad for each size. Some of the sizes can be the same ad, but most should be unique of in the same ad family.

```html
<!DOCTYPE html>
<html lang="en">
<head>
<meta charset="UTF-8">
<title>Sunleaf Pressery – Leaderboard</title>
<link href="https://fonts.googleapis.com/css2?family=Open+Sans:wght@600;700&display=swap" rel="stylesheet">
<style>
  :root {
    --green-light: #a6d553;
    --green: #8cc63f;
    --green-deep: #6aae2e;
    --sky-top: #a7cdee;
    --sky-mid: #d3e6f5;
    --sky-low: #f0f6fb;
    --text-grey: #4d4d4d;
    --white: #ffffff;
    --products-warm: #f1d08a;
    --products-green: #b9d494;
    --products-pale: #ece6dc;
    --model-tone: #f0cfb6;
    --ink: #2f2f2f;
  }
  * { margin: 0; padding: 0; box-sizing: border-box; }
  html, body { width: 1200px; height: 111px; overflow: hidden; background: var(--white); }
  .banner {
    position: relative;
    width: 1200px;
    height: 111px;
    overflow: hidden;
    font-family: "Open Sans", Arial, sans-serif;
  }
  .sky {
    position: absolute; inset: 0;
    background: linear-gradient(180deg, var(--sky-top) 0%, var(--sky-mid) 50%, var(--sky-low) 100%);
  }
  .brand-panel { position: absolute; left: 0; top: 0; width: 230px; height: 111px; }
  .brand-mark {
    position: absolute; left: 6px; top: 25px;
    width: 60px; height: 60px;
    border: 3px solid var(--white); border-radius: 50%;
    display: flex; align-items: center; justify-content: center;
    text-align: center;
    color: var(--white); font-weight: 700; font-size: 9px; line-height: 1.15;
  }
  .tagline-lead {
    position: absolute; left: 92px; top: 41px;
    color: var(--white); font-weight: 600; font-size: 21px; line-height: 1; letter-spacing: 0.5px;
    top: 44px;
  }
  .benefits { position: absolute; inset: 0; list-style: none; }
  .benefit {
    position: absolute;
    display: flex; align-items: center; gap: 9px;
    color: var(--text-grey); font-weight: 600; font-size: 18px;
    white-space: nowrap; line-height: 1;
  }
  .benefit svg { width: 19px; height: 19px; flex: none; }
  .products {
    position: absolute; left: 606px; top: 0; width: 336px; height: 111px;
    background: linear-gradient(90deg, var(--products-warm) 0%, var(--products-green) 50%, var(--products-pale) 100%);
  }
  .model {
    position: absolute; left: 985px; top: 0; width: 196px; height: 111px;
    background: var(--model-tone);
  }
  .pack-count {
    position: absolute; left: 1166px; top: 94px;
    color: var(--ink); font-weight: 700; font-size: 12px; line-height: 1;
  }
</style>
</head>
<body>
<div class="banner">
  <div class="sky" role="img" aria-label="Bright blue sky with soft white clouds"></div>

  <svg class="brand-panel" viewBox="0 0 230 111" aria-hidden="true">
    <defs>
      <linearGradient id="panelGreen" x1="0" y1="0" x2="1" y2="0">
        <stop offset="0" stop-color="#6aae2e"/>
        <stop offset="1" stop-color="#8cc63f"/>
      </linearGradient>
    </defs>
    <path d="M0 0 H212 Q232 55 212 111 H0 Z" fill="#a6d553"/>
    <path d="M0 0 H202 Q222 55 202 111 H0 Z" fill="url(#panelGreen)"/>
  </svg>
  <div class="brand-mark">Sunleaf<br>Pressery</div>
  <div class="tagline-lead">WE ARE</div>

  <ul class="benefits">
    <li class="benefit" style="left:229px; top:12px;">
      <svg viewBox="0 0 18 18"><circle cx="9" cy="9" r="9" fill="#8cc63f"/><path d="M5 9.3l2.8 2.7L13 6.3" fill="none" stroke="#fff" stroke-width="2.2" stroke-linecap="round" stroke-linejoin="round"/></svg>ORGANIC
    </li>
    <li class="benefit" style="left:229px; top:46px;">
      <svg viewBox="0 0 18 18"><circle cx="9" cy="9" r="9" fill="#8cc63f"/><path d="M5 9.3l2.8 2.7L13 6.3" fill="none" stroke="#fff" stroke-width="2.2" stroke-linecap="round" stroke-linejoin="round"/></svg>RAW
    </li>
    <li class="benefit" style="left:229px; top:79px;">
      <svg viewBox="0 0 18 18"><circle cx="9" cy="9" r="9" fill="#8cc63f"/><path d="M5 9.3l2.8 2.7L13 6.3" fill="none" stroke="#fff" stroke-width="2.2" stroke-linecap="round" stroke-linejoin="round"/></svg>COLD PRESSED
    </li>
    <li class="benefit" style="left:412px; top:12px;">
      <svg viewBox="0 0 18 18"><circle cx="9" cy="9" r="9" fill="#8cc63f"/><path d="M5 9.3l2.8 2.7L13 6.3" fill="none" stroke="#fff" stroke-width="2.2" stroke-linecap="round" stroke-linejoin="round"/></svg>NO HPP
    </li>
    <li class="benefit" style="left:412px; top:46px;">
      <svg viewBox="0 0 18 18"><circle cx="9" cy="9" r="9" fill="#8cc63f"/><path d="M5 9.3l2.8 2.7L13 6.3" fill="none" stroke="#fff" stroke-width="2.2" stroke-linecap="round" stroke-linejoin="round"/></svg>GLASS BOTTLE
    </li>
  </ul>

  <div class="products" role="img" aria-label="Row of bottled cold pressed juices, soups and shots in glass"></div>
  <div class="model" role="img" aria-label="Smiling woman pointing toward the product lineup"></div>
  <div class="pack-count">X14</div>
</div>
</body>
</html>
```